Business Card Update, need to bring life to the card, two sided color

We need a new business card design, are moving and changing addresses and need a new look, we have the logos already attached but need a new style moving forward. Can incorporate the color of the logo (The Green) as well, maybe a solid back? We deal with safety products revolving around static electricity and safety lighting. Would like to keep same font in second logo as well.

Target Market(s)

Electrical Safety, Lighting

Contact Information for Business Card

Dale Fenwick
Vice President
Office: 770-555-4821
Cell: 770-555-3067
dale@tkfenwick.example
www.tkfenwick.example
4700 West Harbor Boulevard
Suite #150
Roswell, GA 30076

Font styles to use
Serif
Sans Serif

Requirements
Must have
• Since 1918
Nice to have
• Could use the 100 Year Logo for back of card, would like the back of card to be the same green as logo.
Should not have
• No black cards please.

```html
<!DOCTYPE html>
<html lang="en">
<head>
<meta charset="utf-8">
<title>Business Card – Front and Back</title>
<link href="https://fonts.googleapis.com/css2?family=Open+Sans:wght@400;600;700&display=swap" rel="stylesheet">
<style>
  :root {
    --brand-green: #00894f;
    --brand-green-light: #009a5a;
    --ink: #2b2b2b;
    --paper: #ffffff;
    --paper-shade: #eeeeee;
    --backdrop: #e4e6e5;
  }
  * { margin: 0; padding: 0; box-sizing: border-box; }
  html, body {
    width: 1200px; height: 900px; overflow: hidden;
    background: var(--backdrop);
    font-family: "Open Sans", Arial, sans-serif;
  }
  .sheet { position: relative; width: 1200px; height: 900px; }
  .card {
    position: absolute; left: 280px; width: 640px; height: 366px;
    border-radius: 18px; overflow: hidden;
    box-shadow: 0 10px 26px rgba(0,0,0,0.18);
  }
  .card--front {
    top: 64px;
    background: radial-gradient(circle at 62% 60%, var(--paper) 0%, var(--paper) 40%, var(--paper-shade) 100%);
    color: var(--ink);
  }
  .card--back {
    top: 470px;
    background: linear-gradient(135deg, var(--brand-green-light), var(--brand-green));
  }
  .contact-block { position: absolute; left: 48px; top: 34px; }
  .person-name { color: var(--brand-green); font-weight: 700; font-size: 24px; line-height: 1.15; }
  .person-title { font-size: 16px; line-height: 1.35; }
  .divider { width: 32px; height: 2px; background: var(--brand-green); margin: 14px 0; }
  .address { font-size: 15px; line-height: 1.4; }
  .contact-list { list-style: none; font-size: 15px; line-height: 1.6; }
  .contact-list li { display: flex; align-items: center; gap: 10px; white-space: nowrap; }
  .contact-list svg { width: 13px; height: 13px; flex: none; }
  .contact-label { color: var(--brand-green); font-weight: 600; }
  .web-domain { color: var(--brand-green); }
  .brand {
    position: absolute; display: flex; align-items: center; gap: 14px;
    font-weight: 700; line-height: 1.15; white-space: nowrap;
  }
  .brand-mark { border-radius: 50%; flex: none; }
  .card--front .brand { right: 36px; bottom: 38px; color: var(--brand-green); }
  .card--front .brand-mark { width: 56px; height: 56px; background: var(--brand-green); }
  .card--front .brand-name { font-size: 22px; }
  .card--front .brand-sub { font-size: 12px; display: block; }
  .card--back .brand { left: 50%; top: 46%; transform: translate(-50%, -50%); color: var(--paper); }
  .card--back .brand-mark { width: 96px; height: 96px; background: var(--paper); }
  .card--back .brand-name { font-size: 34px; }
  .card--back .brand-sub { font-size: 16px; display: block; }
  .since {
    position: absolute; left: 0; right: 0; bottom: 70px;
    text-align: center; color: var(--paper);
    font-size: 15px; font-weight: 600; letter-spacing: 3px; text-transform: uppercase;
  }
</style>
</head>
<body>
<main class="sheet">
  <section class="card card--front" aria-label="Card front">
    <div class="contact-block">
      <p class="person-name">Dale Fenwick</p>
      <p class="person-title">Vice President</p>
      <div class="divider"></div>
      <p class="address">4700 West Harbor Boulevard<br>Suite #150<br>Roswell, GA 30076</p>
      <div class="divider"></div>
      <ul class="contact-list">
        <li><svg viewBox="0 0 16 16"><path d="M4 1l3 3-2 2c1 2 3 4 5 5l2-2 3 3-2 3C7 15 1 9 1 3z" fill="var(--brand-green)"/></svg><span><span class="contact-label">Office</span> 770-555-4821</span></li>
        <li><svg viewBox="0 0 16 16"><rect x="4" y="1" width="8" height="14" rx="1.5" fill="none" stroke="var(--brand-green)" stroke-width="1.6"/><circle cx="8" cy="12.5" r="1" fill="var(--brand-green)"/></svg><span><span class="contact-label">Cell</span> 770-555-3067</span></li>
        <li><svg viewBox="0 0 16 16"><rect x="1" y="3" width="14" height="10" fill="none" stroke="var(--brand-green)" stroke-width="1.6"/><path d="M1 3l7 6 7-6" fill="none" stroke="var(--brand-green)" stroke-width="1.6"/></svg><span>dale@tkfenwick.example</span></li>
        <li><svg viewBox="0 0 16 16"><circle cx="8" cy="8" r="7" fill="var(--brand-green)"/></svg><span>www.<span class="web-domain">tkfenwick.example</span></span></li>
      </ul>
    </div>
    <div class="brand">
      <span class="brand-mark"></span>
      <p class="brand-name">T.K. Fenwick<span class="brand-sub">Manufacturing Company, Inc.</span></p>
    </div>
  </section>

  <section class="card card--back" aria-label="Card back">
    <div class="brand">
      <span class="brand-mark"></span>
      <p class="brand-name">T.K. Fenwick<span class="brand-sub">Manufacturing Company, Inc.</span></p>
    </div>
    <p class="since">Since 1918</p>
  </section>
</main>
</body>
</html>
```